Creation of a construction/bricklaying business website

Following the template format of "Halloway 7", the following content would need to be included:
1. Landing page with 3 tiles that go to their own pages.
- Landing page to include background photo and description of services offered.
2. 3 tiles to include:
a) "Contact Us For A Free Quote or Friendly Discussion" Form (middle tile)
b) Case Studies and Testimonials
c) Certifications and Professional Membership
- Design logo to be used from previous SketchNestle project. Example of logo attached below, please access full JPG files from our account.

Target Market(s)

Prospective clients seeking construction work (bricklaying speciality)

Industry/Entity Type

Residential Construction

Coding

Coded - Design and coding required

Number of Pages Required

4 page

Font styles to use
Sans Serif

Colors

Designer to choose colors to be used in the design.

Requirements
Must have
• Following the template format of "Halloway 7", the following content would need to be included:
• 1. Landing parent page with 3 tiles that go to the 3 child pages.
• - Landing page to include background photo and description of services offered.
• 2. 3 tiles to include:
• a) "Contact Us For A Free Quote or Friendly Discussion" Form (middle tile)
• b) Case Studies and Testimonials (first tile / left side)
• c) Certifications and Professional Memberships (third tile / right side) (This should include logos of the relevant organisations being displayed. Specifically plain badge and the Pillar Seal GQT).
• - Design logo to be used from previous SketchNestle project. Example of logo attached below, please access full JPG files from our account.
Nice to have
• Sleek and modern feel.
• Approachable in terms of how people can contact the company for a quote.
• Traditional pictures to give credibility and comfort around choosing this company.
Should not have
• Cheesy pictures
• Over-complicated
• Simple to use
• Easy URL domain name

```html
<!DOCTYPE html>
<html lang="en">
<head>
<meta charset="utf-8">
<title>R. T. Marlow Construction Ltd</title>
<link rel="stylesheet" href="https://fonts.googleapis.com/css2?family=Libre+Franklin:wght@400;500;600;700&display=swap">
<style>
:root{
  --navy:#0d3a7a;
  --navy-deep:#0a2f63;
  --ink:#1c2430;
  --muted:#6b7480;
  --line:#d9dde3;
  --paper:#ffffff;
  --soft:#f3f4f6;
  --btn:#0f58b8;
  --shade:rgba(0,0,0,.74);
}
*{box-sizing:border-box;margin:0;padding:0}
html,body{width:1200px;height:3571px;overflow:hidden}
body{position:relative;background:var(--paper);font-family:"Libre Franklin",Arial,sans-serif;color:var(--ink)}
.abs{position:absolute}
.site-header{left:0;top:0;width:1200px;height:128px;background:var(--paper)}
.brand{left:88px;top:42px;font-size:30px;font-weight:700;color:var(--navy);display:flex;align-items:center;gap:12px}
.brand-mark{width:22px;height:22px;background:var(--navy)}
.header-phone{right:300px;top:26px;font-size:20px;color:var(--navy);display:flex;align-items:center;gap:8px}
.header-cta{right:88px;top:20px;width:146px;height:38px;background:var(--navy);color:#fff;font-size:15px;display:flex;align-items:center;justify-content:center}
.main-nav{right:88px;top:80px;display:flex;gap:34px;font-size:16px;color:var(--ink)}
.hero{left:0;top:128px;width:1200px;height:498px;background:linear-gradient(120deg,#8c8a86,#c9c4bb 45%,#6e6a64)}
.hero h1{left:88px;top:272px;width:600px;font-size:36px;font-weight:400;line-height:1.25;color:#fff}
.hero h1 b{font-weight:700}
.btn-dark{background:var(--ink);color:#fff;font-size:15px;display:flex;align-items:center;justify-content:center}
.hero-arrow{width:40px;height:40px;border-radius:50%;background:rgba(255,255,255,.85)}
.dot{width:12px;height:12px;border-radius:50%;border:2px solid #fff}
.dot.on{background:#fff}
.welcome{left:0;top:626px;width:600px;height:453px;background:var(--soft)}
.welcome small{left:88px;top:726px;font-size:16px;color:var(--muted)}
.welcome-title{left:88px;top:752px;font-size:30px;font-weight:500;color:var(--ink)}
.welcome-title span{color:var(--navy)}
.welcome-text{left:88px;top:800px;width:430px;font-size:14px;line-height:1.6;color:var(--muted)}
.btn-navy{background:var(--navy);color:#fff;font-size:15px;display:flex;align-items:center;justify-content:center}
.photo{background:linear-gradient(160deg,#b9c3cf,#8a8d8f 55%,#5d5a55)}
.services{left:0;top:1079px;width:1200px;height:581px;background:var(--navy)}
.card-title{font-size:17px;font-weight:600;color:#fff}
.card-text{font-size:14px;line-height:1.55;color:#d5def0;width:320px}
.btn-outline{border:1px solid #fff;color:#fff;font-size:14px;display:flex;align-items:center;justify-content:center;width:130px;height:38px}
.testimonial{left:240px;top:1826px;width:720px;text-align:center;font-size:16px;line-height:1.55;color:var(--muted)}
.section-title{width:1200px;text-align:center;font-size:30px;font-weight:400;color:var(--ink)}
.section-title b{color:var(--navy);font-weight:600}
.case-title{font-size:17px;font-weight:600;color:var(--ink);text-decoration:underline;width:260px;line-height:1.35}
.case-date{font-size:14px;color:var(--muted)}
.dot-dark{width:12px;height:12px;border-radius:50%;border:2px solid var(--navy)}
.dot-dark.on{background:var(--navy)}
.badge{width:110px;height:66px;border:1px solid var(--line);display:flex;align-items:center;justify-content:center}
.badge i{display:block;width:60px;height:40px;background:#3a3a3a}
.badge i.red{background:#b3202e}
.cta-band{left:0;top:2962px;width:1200px;height:138px;background:var(--navy)}
.cta-band h3{left:174px;top:2998px;font-size:24px;font-weight:400;color:#fff}
.cta-band p{left:174px;top:3042px;font-size:14px;color:#cfd9ee}
.btn-light{background:#e8ebf0;color:var(--navy);font-size:14px;font-weight:600;display:flex;align-items:center;justify-content:center}
.col-label{font-size:15px;font-weight:600;color:var(--ink)}
.col-text{font-size:14px;line-height:1.6;color:var(--muted)}
.social{width:36px;height:36px;border-radius:50%;border:1px solid var(--navy)}
.social.on{background:var(--navy)}
.footer-nav{left:0;top:3428px;width:1200px;display:flex;justify-content:center;gap:40px;font-size:15px;color:var(--muted)}
.copyright{left:0;top:3520px;width:1200px;text-align:center;font-size:13px;color:var(--muted)}
.overlay{left:0;top:0;width:1200px;height:3571px;background:var(--shade)}
.modal{left:405px;top:1529px;width:383px;height:533px;background:var(--paper)}
.modal h2{position:absolute;left:0;top:20px;width:383px;text-align:center;font-size:21px;font-weight:500;color:var(--ink)}
.modal h2 b{font-weight:700}
.field{position:absolute;left:31px;width:321px;height:30px;border:1px solid var(--line);font-size:11px;color:#8a9099;padding:8px 8px}
.field em{color:#d22;font-style:normal}
.modal-close{left:763px;top:1506px;width:32px;height:32px;border-radius:50%;background:var(--btn);border:3px solid #fff;color:#fff;font-size:14px;display:flex;align-items:center;justify-content:center}
.modal-submit{position:absolute;left:31px;top:476px;width:321px;height:30px;background:var(--btn);color:#fff;font-size:14px;font-weight:600;display:flex;align-items:center;justify-content:center}
</style>
</head>
<body>

<header class="abs site-header">
  <div class="abs brand"><span class="brand-mark"></span>R. T. Marlow</div>
  <div class="abs header-phone">Call Us:
    <svg width="20" height="20" viewBox="0 0 24 24"><path d="M6.6 10.8a15 15 0 006.6 6.6l2.2-2.2a1 1 0 011-.25 11.4 11.4 0 003.6.57 1 1 0 011 1V20a1 1 0 01-1 1A17 17 0 013 4a1 1 0 011-1h3.5a1 1 0 011 1 11.4 11.4 0 00.57 3.6 1 1 0 01-.25 1z" fill="var(--navy)"/></svg>
    07700900461</div>
  <div class="abs header-cta">Get a Quote</div>
  <nav class="abs main-nav"><span>Home ⌄</span><span>About Us</span><span>Services</span><span>Case Studies</span><span>Testimonials</span><span>Certifications</span><span>Contact Us</span></nav>
</header>

<section class="abs hero" role="img" aria-label="Photo of a bright open-plan living room in a renovated home"></section>
<h1 class="abs hero" style="background:none;height:auto;left:88px;top:272px;width:600px;font-size:36px;font-weight:400;line-height:1.25;color:#fff">We believe in <b>full transparency</b> and this is reflected in the <b>jobs we quote for you.</b></h1>
<div class="abs btn-dark" style="left:88px;top:434px;width:146px;height:38px">Explore More</div>
<div class="abs hero-arrow" style="left:1072px;top:332px"></div>
<div class="abs hero-arrow" style="left:1072px;top:380px"></div>
<div class="abs dot" style="left:572px;top:568px"></div>
<div class="abs dot on" style="left:592px;top:568px"></div>
<div class="abs dot" style="left:612px;top:568px"></div>

<section class="abs welcome"></section>
<small class="abs" style="left:88px;top:726px;font-size:16px;color:var(--muted)">Welcome to</small>
<div class="abs welcome-title">R. T. <span>Marlow</span> Construction Ltd</div>
<p class="abs welcome-text">We are a family-run building firm based in the south east, focused on quality brickwork, extensions and new homes. Every quote is itemised so you know exactly where your money goes, and every job is finished with care.</p>
<div class="abs btn-navy" style="left:88px;top:938px;width:148px;height:40px">Explore More</div>

<section class="abs services"></section>
<div class="abs photo" style="left:600px;top:626px;width:600px;height:507px" role="img" aria-label="Photo of a newly built two-storey brick house"></div>

<div class="abs photo" style="left:88px;top:1190px;width:322px;height:184px" role="img" aria-label="Photo of a house extension under construction"></div>
<div class="abs photo" style="left:438px;top:1190px;width:324px;height:184px" role="img" aria-label="Photo of a new build house with scaffolding"></div>
<div class="abs photo" style="left:788px;top:1190px;width:324px;height:184px" role="img" aria-label="Photo of a finished brick garden wall"></div>
<div class="abs card-title" style="left:88px;top:1400px">Extensions</div>
<div class="abs card-title" style="left:438px;top:1400px">New Build / New Houses</div>
<div class="abs card-title" style="left:788px;top:1400px">Garden Walls</div>
<p class="abs card-text" style="left:88px;top:1434px">Contrary to popular belief, Lorem Ipsum is not simply random text. It has roots in a piece of classical Latin literature from 45 BC, making it over 2000 years old…</p>
<p class="abs card-text" style="left:438px;top:1434px">Contrary to popular belief, Lorem Ipsum is not simply random text. It has roots in a piece of classical Latin literature from 45 BC, making it over 2000 years old…</p>
<p class="abs card-text" style="left:788px;top:1434px">Contrary to popular belief, Lorem Ipsum is not simply random text. It has roots in a piece of classical Latin literature from 45 BC, making it over 2000 years old…</p>
<div class="abs btn-outline" style="left:88px;top:1548px">Read More</div>
<div class="abs btn-outline" style="left:438px;top:1548px">Read More</div>
<div class="abs btn-outline" style="left:788px;top:1548px">Read More</div>

<p class="abs testimonial">I asked R. T. Marlow Construction to rebuild the front wall and path to my property. This job consisted of clearing the old brickwork and laying new footings. The finished product was very good and I would strongly recommend them.</p>

<h2 class="abs section-title" style="left:0;top:2180px">Case <b>Studies</b></h2>
<div class="abs photo" style="left:88px;top:2243px;width:322px;height:183px" role="img" aria-label="Photo of a retaining boundary wall"></div>
<div class="abs photo" style="left:438px;top:2243px;width:324px;height:183px" role="img" aria-label="Photo of a parapet wall"></div>
<div class="abs photo" style="left:788px;top:2243px;width:324px;height:183px" role="img" aria-label="Photo of a new brick wall"></div>
<div class="abs case-title" style="left:88px;top:2450px">Built retaining boundary wall in ealing.</div>
<div class="abs case-title" style="left:438px;top:2450px">Built parapet wall in chiswick</div>
<div class="abs case-title" style="left:788px;top:2450px;text-decoration:none">Built new brick wall in ealing, london</div>
<div class="abs case-date" style="left:88px;top:2512px">24/05/2018</div>
<div class="abs case-date" style="left:438px;top:2512px">09/07/2018</div>
<div class="abs case-date" style="left:788px;top:2512px">01/03/2018</div>
<div class="abs dot-dark" style="left:576px;top:2550px"></div>
<div class="abs dot-dark on" style="left:594px;top:2550px"></div>
<div class="abs dot-dark" style="left:612px;top:2550px"></div>

<h2 class="abs section-title" style="left:0;top:2702px">Certifications &amp; <b>Memberships</b></h2>
<div class="abs badge" style="left:190px;top:2800px"><i></i></div>
<div class="abs badge" style="left:355px;top:2800px"><i></i></div>
<div class="abs badge" style="left:530px;top:2800px"><i style="background:#222"></i></div>
<div class="abs badge" style="left:715px;top:2800px"><i class="red"></i></div>
<div class="abs badge" style="left:875px;top:2800px"><i style="background:#222"></i></div>

<section class="abs cta-band"></section>
<h3 class="abs" style="left:174px;top:2998px;font-size:24px;font-weight:400;color:#fff">Get A <b>Free Quote</b></h3>
<p class="abs" style="left:174px;top:3042px;font-size:14px;color:#cfd9ee">Feel free to get in touch and we can talk through what you are looking to achieve …</p>
<div class="abs btn-light" style="left:857px;top:3014px;width:167px;height:38px">Get A Quote Now!</div>

<h2 class="abs section-title" style="left:0;top:3180px">Contact <b>Us</b></h2>
<div class="abs col-label" style="left:88px;top:3270px">Address:</div>
<p class="abs col-text" style="left:88px;top:3300px">12 Harrow Lane, Millbrook<br>Kent, ML2 3QT</p>
<div class="abs col-label" style="left:438px;top:3270px">Call Us:</div>
<div class="abs" style="left:438px;top:3298px;font-size:24px;color:var(--ink)">07700900461</div>
<div class="abs col-text" style="left:438px;top:3332px">Email Us: hello@rtmarlow.example</div>
<div class="abs col-label" style="left:788px;top:3270px">Get Social</div>
<div class="abs social" style="left:788px;top:3310px"></div>
<div class="abs social on" style="left:836px;top:3310px"></div>
<div class="abs social" style="left:884px;top:3310px"></div>
<div class="abs social" style="left:932px;top:3310px"></div>
<svg class="abs" style="left:1078px;top:3318px" width="38" height="38" viewBox="0 0 38 38"><rect x="2" y="2" width="34" height="34" rx="6" fill="none" stroke="var(--ink)" stroke-width="2"/><path d="M19 28V11M12 18l7-7 7 7" fill="none" stroke="var(--ink)" stroke-width="2"/></svg>

<nav class="abs footer-nav"><span>Home ⌄</span><span>About Us</span><span>Services</span><span>Case Studies</span><span>Testimonials</span><span>Certifications</span><span>Contact Us</span></nav>
<div class="abs copyright">© 2018 R. T. Marlow Construction Ltd. All Right Reserved. · Privacy Policy | Legal</div>

<div class="abs overlay"></div>

<form class="abs modal">
  <h2>Get A <b>Free Quote</b></h2>
  <div class="field" style="top:61px"><em>*</em> Your Full Name</div>
  <div class="field" style="top:109px"><em>*</em> Email address</div>
  <div class="field" style="top:157px"><em>*</em> Phone</div>
  <div class="field" style="top:205px"><em>*</em> Post Code</div>
  <div class="field" style="top:247px;height:69px"><em>*</em> Description of the job required</div>
  <div class="field" style="top:331px">Upload pictures of job site
    <svg style="position:absolute;right:0;top:0" width="40" height="28" viewBox="0 0 40 28"><rect width="40" height="28" fill="#eceef1"/><path d="M20 19V9M16 13l4-4 4 4M14 20h12" fill="none" stroke="#6b7480" stroke-width="1.5"/></svg></div>
  <div class="field" style="top:378px">Ideal budget</div>
  <div class="field" style="top:426px">Job start &amp; completion dates</div>
  <div class="modal-submit">Get a Quote Now!</div>
</form>
<div class="abs modal-close">✕</div>

</body>
</html>
```